Natural healthcare clinic needs stationery and business card design

We have had a logo developed by Pixel Harbor and are now looking at utilising it for a new business concept. The concept is a natural healthcare clinic that hosts a number of small businesses. The individual practitioners may want to utilise the host business stationery to provide a consistent message to clients.

I am looking for a stationery design - letterhead, DL brochure template and business card that uses our logo. The business name 'Bright Meadows' is all about getting rhythm back into your life so you can be fit and healthy. The stationery design should reflect this.

There are a couple of requirements for the business card, it needs to be double-sided with black and white back. There should be lines to write appointment times on. The cards may need to be custom named on the front for example Carol Fenwick, Remedial Therapist and Aromatherapist. Therefore if a template can be provided so we can customise this information using MS Publisher, it would be appreciated.

The DL brochure template needs to be A4 folded to DL. I am looking for a consistent brand message that can be utilised to produce our own clinic brochures.

The natural healthcare clinic will host the following types of businesses - remedial massage, pregnancy massage, oncology massage, aromatherapy, acupuncture - as a bit of a guide.

Target Market(s)

25-45 year old male and females who work full time.

Industry/Entity Type

Healthcare

Requirements
Must have
• Use the logo I have already.

```html
<!DOCTYPE html>
<html lang="en">
<head>
<meta charset="utf-8">
<title>Bright Meadows – Appointment Card</title>
<link rel="stylesheet" href="https://fonts.googleapis.com/css2?family=Arimo:ital,wght@0,400;0,700;1,700&display=swap">
<style>
  :root {
    --page-bg: #e9e9e7;
    --card-white: #f4f4f2;
    --card-dark: #2c2b2c;
    --olive: #7d9a2e;
    --olive-deep: #6b8624;
    --logo-light: #b9b68c;
    --leaf: #8cae45;
  }
  * { box-sizing: border-box; margin: 0; padding: 0; }
  html, body {
    width: 1200px; height: 784px; overflow: hidden;
    background: var(--page-bg);
    font-family: "Arimo", Arial, sans-serif;
  }
  .sheet {
    width: 1200px; height: 784px;
    display: flex; align-items: center; justify-content: center; gap: 56px;
  }
  .card {
    width: 540px; height: 310px; position: relative;
    box-shadow: 0 6px 20px rgba(0,0,0,.18);
  }
  .card--front { background: var(--card-white); color: var(--olive); padding: 34px 38px; }
  .card--back { background: var(--card-dark); display: flex; align-items: center; justify-content: center; }

  .brand { display: flex; align-items: center; gap: 10px; font-weight: 400; }
  .brand__dot { border-radius: 50%; background: var(--leaf); flex: none; }
  .card--front .brand { position: absolute; top: 28px; right: 34px; font-size: 17px; color: var(--olive); }
  .card--front .brand__dot { width: 22px; height: 22px; }
  .card--back .brand { font-size: 40px; color: var(--logo-light); letter-spacing: -.5px; }
  .card--back .brand__dot { width: 46px; height: 46px; }

  .appointment { font-size: 22px; line-height: 1.7; }
  .appointment__line { display: flex; align-items: baseline; gap: 6px; }
  .appointment__rule { width: 150px; border-bottom: 2px dotted var(--olive); }

  .practitioner { margin-top: 18px; }
  .practitioner__name { font-size: 25px; font-weight: 700; color: var(--olive-deep); line-height: 1.1; }
  .practitioner__role { font-size: 15px; font-weight: 700; font-style: italic; color: var(--olive-deep); margin-top: 2px; }
  .practitioner__services { font-size: 14px; line-height: 1.35; margin-top: 8px; max-width: 300px; }

  .contact { position: absolute; left: 38px; bottom: 24px; font-size: 15px; line-height: 1.4; }
</style>
</head>
<body>
<main class="sheet">
  <section class="card card--front" aria-label="Appointment card front">
    <div class="brand"><span class="brand__dot"></span>Bright Meadows</div>
    <div class="appointment">
      <div class="appointment__line">Date:<span class="appointment__rule"></span></div>
      <div class="appointment__line">Time:<span class="appointment__rule"></span></div>
    </div>
    <div class="practitioner">
      <h1 class="practitioner__name">Carol Fenwick</h1>
      <p class="practitioner__role">Therapist and Aromatherapist</p>
      <p class="practitioner__services">remedial massage, pregnancy massage, oncology massage, aromatherapy</p>
    </div>
    <div class="contact">
      <p>Address: xxxxxxxxxx</p>
      <p>Phone: xxxxxxxxxx</p>
    </div>
  </section>

  <section class="card card--back" aria-label="Card back">
    <div class="brand"><span class="brand__dot"></span>Bright Meadows</div>
  </section>
</main>
</body>
</html>
```